Velvet Ladle Wishes Website Design; Cupcake Business with a unique and bespoke design element

We need a website design for a new bespoke and unique business making gourmet cupcakes - but MOST IMPORTANTLY we design and handmake cupcake wrappers and toppers specifically for each client's event. We are based in Sydney, Australia. The final resulting website should be elegant yet whimsical reflecting the notion of dreams and very elegant events eg weddings and very special parties.

We want to eventually have about 5 pages, HOWEVER, this project is specifically for the first page (ie Home page) and one other only. The final required pages are: a HOME page; ABOUT US page; PHOTO GALLERY page; FLAVOUR MENU & OTHER PRODUCTS page; CONTACT & INTERNET ENQUIRY page.

We expect the HOME page to be quite elaborate, perhaps including some animation. We will be providing the text content for all the other pages, and basically they will have the same background as the home page. We are looking for a clean design that runs across each page thus giving the website a continuity that pulls it all together. We would like our logo to be included on each page.

PLEASE NOTE: We will want multiple pages worked on in the handover phase but initially we want a very concise, consistent template to limit the amount of work to prospective designers.

While we are primarily looking for the design phase to be covered by this project, we would certainly appreciate coding to be included and will take that into consideration when choosing a winner.
Updates

Hi Designers

We have added some more information to our brief - please review it.

Thanks and happy designing

Hi Designers

Please note that we have increased our Prize money to $750.00.  We hope this encourages you to participate.

Thanks and regards
Velvet Ladle Wishes

Hi Designers

We've just posted some photos to help give you an idea of what we do.  Please note our attention to detail and precision in our work.

Thanks
Velvet Ladle Wishes

Hi Designers

Please Note:  What makes us different  to any other cupcake business is that we design cupcake wrappers and toppers, unique to our client's event whether it be a wedding, a birthday party or product launch.  We consult with our client to understand themes, colours, styles etc.  We then have our designs printed, next they are cut by a specialised computerised cutting machine,  We assemble everything by hand, and usually embellish the wrapper and topper with pearls, crystals, feathers, lace, ribbons or whatever else is appropriate for the event.  All work is totally bespoke, unique and individual.  No other cupcake supplier that we know of goes to these lengths to satisfy their client's dreams.

THE WRAPPER AND TOPPER IS OUR PRIMARY SELLING POINT. 

PLEASE NOTE:- We have uploaded a new photograph which we want to be used as the main photograph on the landing page.

We have removed all previous photographs of cupcakes (except for one that we can't get rid of).

We don't want a picture of a cupcake on the landing page we want the image _D7C3239.jpg to be used for that purpose.

We have also uploaded our logo in a number of file formats as we have had requests from you for these.

Hi designers

we have a crazy busy weekend on and won't be able to make any decisions re our competition until Monday  -  sorry to keep you in suspense, just a couple more days please!

regards
Pam

Target Market(s)

Primarily women - brides, new mothers (Christenings), Event Planners, who place an emphasis on the beauty of a product rather than the cost

Industry/Entity Type

Events

Requirements
Must have
• It must have our Logo (see attached upload) on each page (our logo is a butterfly atop a cupcake resting on a spoon and our motto is "Creating Delicious Works of Art". The colours used are pale pink, blue and chocolate brown and we'd expect these colours to be repeated in the final website.
The website must have a photo gallery which we can access and add to/change as our business grows.
We need a contact page which has an "internet enquiry form".
There should be a "Menu" page describing our cupcake flavours.
The Home page must have a party/event feel to it - definitely making an enquirer want to enter further into the site.
Nice to have
• Our logo is attached below in the "uploads". One idea that we have had is to use the butterfly in the logo but start it as a caterpillar crawling on the screen; as it spins it's cocoon the words "Sweet Dreams Little Caterpillar" would appear on screen; this would incorporate the "Dreams" in our Business Name; then our logo butterfly would hatch. This encapsulates the idea of taking something plain (caterpillar/cupcake) and creating something beautiful (butterfly/OUR cupcake).
However, we are open to other design ideas.
The colours we would like to have are pale pink, blue and chocolate brown in the design.

Some websites we really admire are: www.mirabellhart.com www.ribbonglitterloaf.com.au and www.greetingsoriel.com.au
These websites have a lightness and sense of fantasy to them. They do not convey a corporate image at all, rather they make you want to be at the party.
Should not have
• No "Corporate" style.

Most Important: We already have a website which we are not happy with - that is why we are going through this exercise to replace it. That means we DO NOT want anything along the lines of our current website. We are expecting some fresh ideas for our prize money.

```html
<!DOCTYPE html>
<html lang="en">
<head>
<meta charset="utf-8">
<title>Velvet Ladle Wishes — Home</title>
<link rel="stylesheet" href="https://fonts.googleapis.com/css2?family=Berkshire+Swash&family=Parisienne&family=Hind:wght@300;400;500&display=swap">
<style>
  :root{
    --bg:#f7d3d9;
    --page:#fbdde2;
    --ribbon:#5a2d36;
    --ribbon-dark:#431d24;
    --ribbon-mid:#6b3f47;
    --pill:#3a181e;
    --pink:#e0136b;
    --brown:#5c2a0c;
    --body:#3a2a2a;
    --blue:#2f6a96;
    --feature:#f8aaae;
    --standard:#6aa2c9;
    --white:#ffffff;
    --footer:#4a2028;
  }
  *{box-sizing:border-box;margin:0;padding:0}
  html,body{width:1200px;height:1025px;overflow:hidden}
  body{background:var(--bg);font-family:'Hind',sans-serif;color:var(--body);position:relative}
  h1,h2,h3{font-weight:400}
  .abs{position:absolute}
  .page{left:155px;top:0;width:890px;height:1025px;background:var(--page)}

  .search{left:773px;top:14px;display:flex;align-items:center;gap:6px;font-size:14px;color:#5b4a4d}
  .search-field{width:165px;height:24px;background:#a58d92;border:1px solid #8c7479;margin-left:6px}
  .search-go{width:28px;height:24px;background:#6aa2c9;color:var(--white);font-size:13px;display:flex;align-items:center;justify-content:center;border-radius:2px}

  .ribbon-tail{top:64px;width:90px;height:42px;background:var(--ribbon)}
  .ribbon-tail.left{left:70px;clip-path:polygon(0 50%,12% 0,100% 0,100% 100%,12% 100%)}
  .ribbon-tail.right{left:1040px;clip-path:polygon(0 0,88% 0,100% 50%,88% 100%,0 100%)}
  .nav-bar{left:122px;top:52px;width:956px;height:46px;background:var(--ribbon-dark);box-shadow:0 6px 10px rgba(60,20,30,.35)}
  .nav-inner{left:130px;top:58px;width:942px;height:32px;background:var(--ribbon-mid)}
  .nav a{position:absolute;top:62px;height:22px;line-height:22px;font-family:'Berkshire Swash',cursive;font-size:14px;color:var(--white);text-decoration:none;transform:translateX(-50%);white-space:nowrap}
  .nav a.active{background:var(--pill);width:71px;text-align:center}

  .brand{left:175px;top:130px;width:380px;height:250px}
  .brand-mark{left:100px;top:0;width:170px;height:170px;border-radius:50%;background:radial-gradient(circle,#f9c6d4,#f4b3c3 60%,rgba(244,179,195,0) 72%)}
  .brand-name{left:0;top:168px;font-weight:500;font-size:38px;color:var(--brown);white-space:nowrap}
  .brand-tag{left:146px;top:219px;font-size:16px;color:var(--pink)}

  .hero-photo{left:705px;top:105px;width:298px;height:325px;border-radius:40px 40px 60px 60px;background:linear-gradient(180deg,#f3e6cf 0%,#e9d6b4 28%,#9a6a50 48%,#5a3a30 62%,#262637 78%,#1d2233 100%);box-shadow:0 14px 24px rgba(220,120,140,.35)}
  .hero-band{left:147px;top:0;width:908px;height:472px}

  .welcome{left:178px;top:494px;font-family:'Parisienne',cursive;font-size:34px;color:var(--blue);white-space:nowrap}
  .lead-pink{left:179px;top:549px;font-size:13px;color:var(--pink)}
  .lead-brown{left:179px;top:567px;font-size:13px;color:var(--brown)}
  .intro{left:179px;top:594px;width:562px;font-size:11px;line-height:16px}
  .why{left:178px;top:708px;font-size:23px;color:var(--blue)}
  .why-lead{left:182px;top:746px;width:540px;font-size:12.5px;line-height:16px;color:var(--pink)}

  .card-photo{width:132px;height:106px;border:1px solid #9c8a8d;background:#fff;padding:3px}
  .card-photo span{display:block;width:100%;height:100%}
  .card-title{font-size:12.5px;color:var(--brown);white-space:nowrap}
  .card-text{width:148px;font-size:11.5px;line-height:16px}

  .panel{left:761px;width:264px;border-radius:3px}
  .panel.featured{top:493px;height:237px;background:var(--feature)}
  .panel.standard{top:734px;height:151px;background:var(--standard)}
  .panel-title{left:40px;font-size:23px;font-weight:400;color:var(--white);white-space:nowrap}
  .panel-rule{position:absolute;left:110px;top:12px;width:92px;border-top:1px solid rgba(255,255,255,.6)}
  .feature-text{left:40px;top:64px;width:222px;font-size:11.5px;line-height:17px;color:#111}
  .feature-photo{left:39px;top:112px;width:98px;height:108px;border-radius:14px;background:linear-gradient(180deg,#f1e2e0 0%,#c98b8e 40%,#7a3036 75%,#b43a55 100%)}
  .feature-links{left:157px;top:108px;width:90px;list-style:none}
  .feature-links li{font-size:11px;color:var(--white);height:22px;line-height:22px;border-bottom:1px dashed rgba(255,255,255,.7)}
  .feature-links li:last-child{border-bottom:none}
  .standard-photo{left:39px;top:59px;width:90px;height:80px;border:2px solid #fff;background:linear-gradient(160deg,#8a6a52,#c99f80 55%,#e8e4df)}
  .standard-text{left:136px;top:63px;width:124px;font-size:11.5px;line-height:16px;color:var(--white)}
  .standard-more{left:139px;top:115px;font-size:11px;color:var(--white);text-decoration:underline}

  .connect{left:773px;top:906px;font-size:11px;color:#4a3a3d}
  .social{top:904px;width:20px;height:20px;border-radius:2px}

  .footer-band{left:45px;top:936px;width:1111px;height:65px;background:var(--ribbon)}
  .footer{left:146px;top:943px;width:908px;height:64px;background:var(--footer);color:var(--white);text-align:center}
  .footer-nav{padding-top:13px;font-size:11.5px}
  .footer-nav span{margin:0 5px}
  .copyright{margin-top:8px;font-size:11px}
</style>
</head>
<body>
  <div class="abs page"></div>

  <div class="abs search">Search<span class="search-field"></span><span class="search-go">Go</span></div>

  <div class="abs ribbon-tail left"></div>
  <div class="abs ribbon-tail right"></div>
  <div class="abs nav-bar"></div>
  <div class="abs nav-inner"></div>
  <nav class="nav">
    <a class="active" style="left:279px" href="#">Home</a>
    <a style="left:382px" href="#">About Us</a>
    <a style="left:496px" href="#">Photo gallery</a>
    <a style="left:619px" href="#">Flavor Menu</a>
    <a style="left:729px" href="#">Products</a>
    <a style="left:822px" href="#">Contact</a>
    <a style="left:914px" href="#">Enquiry</a>
  </nav>

  <svg class="abs hero-band" width="908" height="472" viewBox="0 0 908 472" aria-hidden="true">
    <defs>
      <linearGradient id="band" x1="0" y1="0" x2="0" y2="1">
        <stop offset="0" stop-color="#fbd1d7"/>
        <stop offset="1" stop-color="#f9bcc5"/>
      </linearGradient>
      <pattern id="scallop" width="16" height="16" patternUnits="userSpaceOnUse" x="0" y="452">
        <circle cx="8" cy="8" r="8" fill="#f9bcc5" stroke="#f3aab5"/>
      </pattern>
    </defs>
    <path d="M8 385 H900 L908 460 H0 Z" fill="url(#band)"/>
    <rect x="0" y="452" width="908" height="16" fill="url(#scallop)"/>
    <rect x="0" y="444" width="908" height="16" fill="#f9bcc5"/>
  </svg>

  <div class="abs hero-photo" role="img" aria-label="Photo of a chocolate cupcake with white swirled frosting and butterfly sprinkles"></div>

  <header class="abs brand">
    <div class="abs brand-mark"></div>
    <div class="abs brand-name">Velvet Ladle Wishes</div>
    <div class="abs brand-tag">Creating Delicious Works of Art</div>
  </header>

  <main>
    <h1 class="abs welcome">Welcome to Velvet Ladle Wishes!</h1>
    <p class="abs lead-pink">These cases are perfectly simple and easy to distinguish.</p>
    <p class="abs lead-brown">The wise man therefore always holds in these matters to this principle of selection:</p>
    <p class="abs intro">These cases are perfectly simple and easy to distinguish. In a free hour, when our power of choice is untrammelled and when nothing prevents our being able to do what we like best, every pleasure is to be welcomed and every pain avoided. But in certain circumstances and owing to the claims of duty or the obligations of business it will frequently occur that pleasures have to be repudiated and annoyances accepted. The wise man therefore always holds in these matters to this principle of selection: he rejects pleasures to secure other greater pleasures, or else he endures pains to avoid worse pains</p>

    <h2 class="abs why">Why choose us our bakery?</h2>
    <p class="abs why-lead">These cases are perfectly simple and easy to distinguish.n a free hour, when our power of choice is untrammelled and when nothing prevents</p>

    <div class="abs card-photo" style="left:185px;top:795px"><span role="img" aria-label="Photo of a tiered stand of pink decorated cupcakes" style="background:linear-gradient(160deg,#f3e3e6,#e8899a 60%,#c9485e)"></span></div>
    <h3 class="abs card-title" style="left:322px;top:799px">At vero eos et accusamus</h3>
    <p class="abs card-text" style="left:322px;top:818px">Temporibus autem quibus-dam et aut officiis debitis aut rerum necessitatibus saepe eveniet ut et voluptates repudiandae .</p>

    <div class="abs card-photo" style="left:469px;top:795px"><span role="img" aria-label="Photo of a cupcake with white frosting and a yellow butterfly topper" style="background:linear-gradient(180deg,#3a2a22 0%,#c9a34a 30%,#f3eee8 55%,#5a3a2c 100%)"></span></div>
    <h3 class="abs card-title" style="left:606px;top:799px">At vero eos et accusamus</h3>
    <p class="abs card-text" style="left:606px;top:818px">Temporibus autem quibus-dam et aut officiis debitis aut rerum necessitatibus saepe eveniet ut et voluptates repudiandae .</p>
  </main>

  <aside>
    <section class="abs panel featured">
      <span class="panel-rule"></span>
      <h2 class="abs panel-title" style="top:24px">Featured Category</h2>
      <p class="abs feature-text">The wise man therefore always holds in these matters to this principle of selection:</p>
      <div class="abs feature-photo" role="img" aria-label="Photo of a chocolate cupcake with a white flower topper"></div>
      <ul class="abs feature-links">
        <li>greater pleasures</li><li>greater pleasures</li><li>greater pleasures</li><li>greater pleasures</li><li>greater pleasures</li>
      </ul>
    </section>

    <section class="abs panel standard">
      <span class="panel-rule"></span>
      <h2 class="abs panel-title" style="top:24px">Our Standard</h2>
      <div class="abs standard-photo" role="img" aria-label="Portrait photo of the head baker"></div>
      <p class="abs standard-text">The wise man therefore always holds in these matters to this principle</p>
      <a class="abs standard-more" href="#">more</a>
    </section>
  </aside>

  <div class="abs connect">Connect with us:</div>
  <span class="abs social" style="left:868px;background:#3b5a96"></span>
  <span class="abs social" style="left:895px;background:#6fc3e8"></span>
  <span class="abs social" style="left:922px;background:#f07a2a"></span>
  <span class="abs social" style="left:949px;background:#2a6ea8"></span>
  <span class="abs social" style="left:976px;background:#e7e7e7"></span>

  <div class="abs footer-band"></div>
  <footer class="abs footer">
    <div class="footer-nav">Home<span>|</span>About Us<span>|</span>Photo gallery<span>|</span>Flavor Menu<span>|</span>Products<span>|</span>Contact<span>|</span>Enquiry</div>
    <div class="copyright">© copyrights velvet ladle wishes.All rights Reserved</div>
  </footer>
</body>
</html>
```